Fenlow Systems

Looking for a web site design to market our services/applications
We write and supply bespoke web applications for the offshore and construction industries
Our initial product is Tolv - rope access equipment management
Our buyers will be Rope Access companies via trade associations such as KOBEN and DULMO
we have a logo designed see it attached we would like to see crisp professional designs based around these colours and design
we will supply web copy later
looking for home, services, blog, contact us, order and a general template (privacy, site map, T&C) pages
Updates
This payment will be for the homepage only
We can discuss other options (pages) with the successful designer
Regards
Marcus
Industry/Entity Type
Construction
Look and feel
Each slider illustrates characteristics of the customer's brand and the style your logo design should communicate.

```html
<!DOCTYPE html>
<html lang="en">
<head>
<meta charset="utf-8">
<title>Fenlow Systems – Rope Access Equipment Management</title>
<link rel="stylesheet" href="https://fonts.googleapis.com/css2?family=Varela+Round&family=Open+Sans:wght@400;600&display=swap">
<style>
:root{
  --navy:#0a2a8c;
  --navy-dark:#061e6e;
  --sky:#1a8fd6;
  --sky-bright:#2aa9ee;
  --ink:#555a60;
  --muted:#7c8086;
  --line:#dcdfe3;
  --white:#ffffff;
}
*{box-sizing:border-box;margin:0;padding:0}
html,body{width:1109px;height:1200px;overflow:hidden;background:var(--white)}
body{position:relative;font-family:"Open Sans",Arial,sans-serif;color:var(--ink)}
.abs{position:absolute}
.round{font-family:"Varela Round","Open Sans",sans-serif}

/* header */
.site-header{left:0;top:0;width:1109px;height:109px;background:var(--white)}
.brand-mark{left:142px;top:22px;width:66px;height:64px;border-radius:10px;background:linear-gradient(#f7f8fa,#dfe2e6)}
.brand-divider{left:220px;top:8px;width:1px;height:92px;background:var(--line)}
.brand-name{left:232px;top:36px;font-size:25px;line-height:30px;color:var(--navy);width:220px}
.contact-label{right:139px;top:54px;font-size:14px;color:var(--muted)}
.contact-phone{right:139px;top:70px;font-size:20px;color:#444;display:flex;align-items:center;gap:6px}

/* nav */
.main-nav{left:0;top:109px;width:1109px;height:43px;background:linear-gradient(#0b2f9a,#061f73)}
.main-nav ul{list-style:none;display:flex;height:43px;position:absolute;left:156px}
.main-nav li{color:var(--white);font-size:14px;height:43px;line-height:43px;text-align:center;border-right:1px solid rgba(255,255,255,.35)}
.main-nav li:last-child{border-right:none}

/* hero */
.hero{left:0;top:152px;width:1109px;height:446px;background:linear-gradient(#eceef1 0%,#fff 25%,#fff 70%,#eef0f3 100%)}
.hero-title{left:138px;top:280px;font-size:32px;line-height:33px;color:var(--sky);width:400px;font-weight:400}
.hero-sub{left:138px;top:353px;font-size:20px;color:var(--navy);font-weight:400}
.hero-text{left:138px;top:390px;width:360px;font-size:11px;line-height:18px;color:var(--muted)}
.hero-dots{left:138px;top:441px;display:flex;gap:1px}
.hero-dots span{width:12px;height:12px;border-radius:50%;background:var(--sky-bright)}
.hero-visual{left:566px;top:184px;width:342px;height:414px;border-radius:26px 26px 0 0;background:linear-gradient(160deg,#f4f5f7 0%,#e7e9ec 55%,#d7b39a 100%)}

/* feature cards */
.card{top:626px;width:258px;height:198px;border:1px solid #e1e3e6;background:linear-gradient(#fff,#f4f5f6)}
.card-photo{width:100%;height:117px}
.card-title{font-size:18px;font-weight:400;color:#222;margin:10px 0 0 15px}
.card-text{font-size:10px;line-height:16px;color:var(--muted);margin:3px 15px 0 16px}
.video-card{left:688px;top:626px;width:258px;height:198px}
.video-photo{width:258px;height:155px;background:linear-gradient(135deg,#9fb3c6,#c8d2d9 50%,#9bb47a)}
.video-play{left:108px;top:56px}
.video-band{top:154px;left:0;width:258px;height:44px;background:linear-gradient(#22a3ec,#1180cf);color:var(--white);font-size:18px;line-height:44px;padding-left:18px}

/* about */
.about{left:142px;top:874px;width:540px;display:flex;flex-direction:column}
.about-title{font-size:24px;line-height:30px;font-weight:400;color:var(--navy);margin-bottom:8px;white-space:nowrap}
.about-text{font-size:11px;line-height:18.5px;color:var(--ink);letter-spacing:-0.1px}
.about-text + .about-text{margin-top:8px}
.partners{display:flex;align-items:center;gap:25px;margin-top:12px}
.partner-a{width:113px;height:56px;background:#1c1c1c;border-radius:4px}
.partner-b{width:73px;height:46px;border-radius:50%;border:3px solid #233a7a;background:#f2f3f7}

/* blog */
.blog-title{left:698px;top:874px;font-size:22px;font-weight:400;color:#666}
.blog-item{left:698px;width:270px}
.blog-item h3{font-size:11.5px;font-weight:400;color:var(--sky);margin-bottom:4px}
.blog-item p{font-size:10px;line-height:16.5px;color:var(--muted)}

/* footer */
.site-footer{left:0;top:1104px;width:1109px;height:96px;background:linear-gradient(#0a2d95,#051c6c);color:var(--white)}
.footer-nav{left:146px;top:22px;font-size:13px;color:var(--white);word-spacing:2px}
.footer-copy{left:147px;top:50px;font-size:11px;color:#b9c3e6}
.footer-legal{right:134px;top:22px;font-size:11px;color:#dfe5fb}
.social{right:136px;top:50px;display:flex;gap:6px}
.social span{width:16px;height:16px;border-radius:2px}
</style>
</head>
<body>

<header class="site-header abs">
  <div class="brand-mark abs"></div>
  <div class="brand-divider abs"></div>
  <div class="brand-name abs round">Fenlow<br>Systems</div>
  <div class="contact-label abs round">Contact Us</div>
  <div class="contact-phone abs round">
    <svg width="20" height="20" viewBox="0 0 20 20" aria-hidden="true"><circle cx="10" cy="10" r="9" fill="none" stroke="#1a8fd6" stroke-width="1.6"/><path d="M7 5.5c-.8.5-1.2 1.4-.9 2.6.6 2.4 2.4 4.6 4.6 5.6 1.2.5 2.1.2 2.7-.6l-1.5-1.5-1.2.6c-1-.6-1.8-1.5-2.3-2.5l.6-1.2z" fill="#1a8fd6"/></svg>
    555.014.2278
  </div>
</header>

<nav class="main-nav abs round">
  <ul>
    <li style="width:103px">HOME</li>
    <li style="width:134px">ABOUT US</li>
    <li style="width:129px">SERVICES</li>
    <li style="width:107px">BLOG</li>
    <li style="width:110px">ORDER</li>
    <li style="width:150px">CONTACT US</li>
  </ul>
</nav>

<section class="hero abs"></section>
<h1 class="hero-title abs round">Rope Access Equipment Management</h1>
<h2 class="hero-sub abs round">Morbi porta libero nonummy</h2>
<p class="hero-text abs">Etiam est nunc venenatis in tristique eu imperdiet ac nisl Cum sociis natoque penatibus et magnis dis parturient montes</p>
<div class="hero-dots abs"><span></span><span></span><span></span><span></span></div>
<div class="hero-visual abs" role="img" aria-label="Hand holding a white tablet showing the Fenlow Systems name"></div>

<article class="card abs" style="left:141px">
  <div class="card-photo" role="img" aria-label="Construction workers in hi-vis vests reviewing plans on site" style="background:linear-gradient(135deg,#c9d2da,#e4a65a 45%,#8fa3b8)"></div>
  <h3 class="card-title round">Our Application</h3>
  <p class="card-text">Etiam est nunc venenatis in tristique eu imperd iet ac nisl Cum sociis natoque</p>
</article>
<article class="card abs" style="left:411px">
  <div class="card-photo" role="img" aria-label="Engineer in a hard hat working at a laptop with tools" style="background:linear-gradient(135deg,#e8e6e2,#d9c48a 50%,#6f7f95)"></div>
  <h3 class="card-title round">Our Services</h3>
  <p class="card-text">Etiam est nunc venenatis in tristique eu imperd iet ac nisl Cum sociis natoque</p>
</article>
<article class="video-card abs">
  <div class="video-photo" role="img" aria-label="Two site engineers in hard hats checking a tablet"></div>
  <svg class="video-play abs" width="40" height="40" viewBox="0 0 40 40" aria-hidden="true"><circle cx="20" cy="20" r="20" fill="#fff"/><path d="M16 12l11 8-11 8z" fill="#111"/></svg>
  <div class="video-band abs round">Watch Our Video</div>
</article>

<section class="about abs">
  <h2 class="about-title round">About Rope access equipment management</h2>
  <p class="about-text">Vivamus porttitor g purus nisi eleifend libero a tempus libero lectus feugiat felis Morbi diam mauris viverra in gravida eu mattis in ante Morbi eget arcu Morbi porta libero id ullamcorper nonummy nibh ligula pulvinar metus eget consectetuer augue nisi quis lacus Ut ac mi quis lacus mollis aliquam</p>
  <p class="about-text">Curabitur iaculis tempus eros Curabitur vel mi sit amet magna malesuada ultrices Ut nisi erat fermentum vel congue id euismod in elit Fusce ultricies orci ac feugiat suscipit leo massa</p>
  <div class="partners">
    <div class="partner-a" role="img" aria-label="DULMO trade association badge"></div>
    <div class="partner-b" role="img" aria-label="KOBEN trade association badge"></div>
  </div>
</section>

<h2 class="blog-title abs round">Recent Blog</h2>
<div class="blog-item abs" style="top:906px">
  <h3>Curabitur iaculis tempus</h3>
  <p>Etiam est nunc venenatis in tristique eu imperdiet ac nisl Cum sociis natoque penatibus et</p>
</div>
<div class="blog-item abs" style="top:973px">
  <h3>Nam cursus Morbi ut mi Nullam</h3>
  <p>Cum sociis natoque penatibus et magnis dis parturient montes nascetur ridiculus mus In iaculis facilisis massa Etiam eu urna Sed porta Suspendisse</p>
</div>

<footer class="site-footer abs">
  <div class="footer-nav abs">Home&nbsp; | &nbsp;About Us&nbsp; | &nbsp;Services&nbsp; | &nbsp;Blog&nbsp; | &nbsp;Order&nbsp; | &nbsp;Contact Us</div>
  <div class="footer-copy abs">© 2014 Company Name&nbsp; All right reserved</div>
  <div class="footer-legal abs">Privacy&nbsp; | &nbsp;Sitemap&nbsp; | &nbsp;Term &amp; Conditions</div>
  <div class="social abs" aria-label="Social links">
    <span style="background:#3b5a9a"></span>
    <span style="background:#3fb3e6"></span>
    <span style="background:#1f7bb6"></span>
    <span style="background:#f08a1c"></span>
  </div>
</footer>

</body>
</html>
```